Retail Jewelry Business Card Design Project

We are in need of a new business card design for a retail jewelry store. This store is in the business of fine jewelry including but not specific to bridal jewelry, diamonds, designer jewelry and watches.

This store has been in business for 20 years but continues to strive for a modern professional appeal. The main colors use for this business are a royal blue, white and silver.

Target Market(s)

Target market is ages 18-50

Industry/Entity Type

Jewelry

Requirements
Must have
• Sales Person Name
Sales Person Email Address

Store Address
Store Phone
Website

Standard business card size. No odd shapes or sizes.
Nice to have
• Overall modern feel for card.

We have thought that a design with a nice feature of the logo on the back of the card would be nice but open to ideas.
Should not have
• No specific images of jewelry should be used.

```html
<!DOCTYPE html>
<html lang="en">
<head>
<meta charset="utf-8">
<title>Laurel Grant Fine Jewelry – Business Card</title>
<link href="https://fonts.googleapis.com/css2?family=Open+Sans:wght@400;600&display=swap" rel="stylesheet">
<style>
  :root {
    --page: #ffffff;
    --navy-deep: #0b1222;
    --navy-glow: #122a52;
    --royal: #2e2e8c;
    --royal-light: #6a63c4;
    --band-blue: #34349a;
    --ink: #2b2b2b;
    --black-band: #0d0f18;
    --white: #ffffff;
  }
  * { margin: 0; padding: 0; box-sizing: border-box; }
  html, body {
    width: 1200px; height: 1000px; overflow: hidden;
    background: var(--page);
    font-family: "Open Sans", Arial, sans-serif;
  }
  .card {
    position: absolute; left: 285px; width: 653px; height: 374px;
    border-radius: 28px; overflow: hidden;
    box-shadow: 4px 6px 8px rgba(0,0,0,0.35);
  }
  .card-back {
    top: 102px;
    background: radial-gradient(circle at 52% 40%, var(--navy-glow) 0%, var(--navy-deep) 55%, #080d19 100%);
  }
  .card-front { top: 532px; background: var(--white); }

  .brand { position: absolute; text-align: center; font-weight: 600; line-height: 1.1; }
  .brand-name { font-size: 38px; letter-spacing: 0.5px; }
  .brand-line { font-size: 17px; letter-spacing: 3px; text-transform: uppercase; margin-top: 6px; }
  .card-back .brand { left: 295px; top: 200px; width: 325px; color: var(--white); }
  .card-front .brand { left: 293px; top: 58px; width: 315px; color: var(--royal); }

  .back-web {
    position: absolute; left: 325px; top: 320px;
    color: var(--white); font-size: 15.5px; letter-spacing: 1px;
  }

  .edge-tab {
    position: absolute; left: 0; top: 208px; width: 15px; height: 66px;
    background: var(--black-band); border-radius: 0 12px 12px 0;
  }
  .person { position: absolute; left: 50px; top: 218px; }
  .person-name { font-size: 19.5px; font-weight: 600; color: var(--royal); }
  .person-name .surname { color: var(--royal-light); }
  .person-role { font-size: 15px; color: var(--ink); margin-top: 1px; }

  .contact {
    position: absolute; right: 42px; top: 222px; text-align: right;
    font-size: 15px; color: var(--ink); line-height: 22px;
  }
  .contact-lines { margin-bottom: 13px; }
  .contact-row { display: flex; justify-content: flex-end; align-items: center; gap: 10px; }
  .contact-row svg { width: 17px; height: 14px; fill: var(--royal-light); }

  .footer { position: absolute; left: 0; bottom: 0; width: 653px; height: 34px; }
  .front-web {
    position: absolute; right: 42px; bottom: 8px;
    color: var(--white); font-size: 15.5px; letter-spacing: 0.8px;
  }
</style>
</head>
<body>
  <section class="card card-back">
    <div class="brand">
      <div class="brand-name">Laurel Grant</div>
      <div class="brand-line">Fine Jewelry</div>
    </div>
    <div class="back-web">www.laurelgrantjewelry.com</div>
  </section>

  <section class="card card-front">
    <div class="brand">
      <div class="brand-name">Laurel Grant</div>
      <div class="brand-line">Fine Jewelry</div>
    </div>

    <div class="edge-tab"></div>
    <div class="person">
      <div class="person-name">Laurel Grant <span class="surname">Whitfield</span></div>
      <div class="person-role">Owner</div>
    </div>

    <div class="contact">
      <div class="contact-lines">
        <div>2218 Marlow Avenue</div>
        <div>Bayport, FL 32590</div>
      </div>
      <div class="contact-row">
        <span>000.000.0000</span>
        <svg viewBox="0 0 17 14" aria-hidden="true"><path d="M1 4 C1 1 16 1 16 4 L16 6 L12 6 L12 4 L5 4 L5 6 L1 6 Z"/><path d="M4 7 L13 7 L15 13 L2 13 Z"/></svg>
      </div>
      <div class="contact-row">
        <span>laurel@laurelgrantjewelry.com</span>
        <svg viewBox="0 0 17 14" aria-hidden="true"><path d="M0 1 L17 1 L17 13 L0 13 Z M1.5 2.5 L8.5 8 L15.5 2.5 Z" fill-rule="evenodd"/></svg>
      </div>
    </div>

    <svg class="footer" viewBox="0 0 653 34" aria-hidden="true">
      <rect x="0" y="13" width="330" height="21" fill="var(--band-blue)"/>
      <path d="M308 34 L332 5 Q336 1 342 1 L653 1 L653 34 Z" fill="var(--white)"/>
      <path d="M312 34 L334 8 Q338 3 345 3 L653 3 L653 34 Z" fill="var(--black-band)"/>
    </svg>
    <div class="front-web">www.laurelgrantjewelry.com</div>
  </section>
</body>
</html>
```